World Wide News and Current Affairs website

We intends to start up a new website which deals on New and Current Affairs.
Attention Designers,
We want a home page design for this project. Our business is based in the United States. Our goal is to become a well known brand.
The website would consist of a category for News, Business and Tech.
The theme should be beautiful and attention seeking. The website would take bulk of it's news from the US, and Europe.
Designers can get inspiration from already existing new websites such as PWJ, KLV, DASKOLM.
All designs should be clean and easy to navigate.

```html
<!DOCTYPE html>
<html lang="en">
<head>
<meta charset="utf-8">
<title>Vantora — World News and Current Affairs</title>
<link href="https://fonts.googleapis.com/css2?family=Montserrat:wght@400;600;700&family=Open+Sans:wght@400;600&display=swap" rel="stylesheet">
<style>
:root{
  --blue:#1e88e5;
  --blue-dark:#1565c0;
  --red:#e53935;
  --orange:#ff9800;
  --ink:#222;
  --muted:#8a8a8a;
  --line:#e6e6e6;
  --soft:#f4f4f4;
  --dark:#1c1c1c;
  --darker:#121212;
  --white:#fff;
}
*{box-sizing:border-box;margin:0;padding:0}
html,body{width:1200px;height:4865px;overflow:hidden}
body{position:relative;background:var(--white);font-family:"Open Sans",Arial,sans-serif;font-size:11px;color:var(--ink);line-height:1.5}
h1,h2,h3,h4{font-family:"Montserrat",Arial,sans-serif}
.abs{position:absolute}
.ph{display:block}
.meta{color:var(--muted);font-size:9px}
.title{font-family:"Montserrat",Arial,sans-serif;font-weight:600;font-size:12px;line-height:1.35;color:var(--ink)}
.excerpt{color:var(--muted);font-size:10px;line-height:1.55}
.tag{display:inline-block;background:var(--red);color:#fff;font-size:8px;font-weight:700;padding:2px 6px;text-transform:uppercase;font-family:"Montserrat",sans-serif}
.count{display:inline-block;background:var(--blue);color:#fff;font-size:8px;padding:1px 5px;float:right}

.topbar{top:0;left:0;width:1200px;height:39px;border-bottom:1px solid var(--line);background:#fafafa}
.topbar .inner{position:absolute;left:227px;width:740px;top:0;height:39px;display:flex;align-items:center;justify-content:space-between;font-size:10px;color:#666}
.topbar .links span{margin-right:22px}

.header{top:39px;left:227px;width:740px;height:84px;display:flex;align-items:center;justify-content:space-between}
.logo{display:flex;align-items:center;gap:8px;font-family:"Montserrat",sans-serif;font-weight:700;font-size:24px;color:var(--blue)}
.logo i{display:block;width:22px;height:22px;background:var(--blue);border-radius:50%}
.search{width:290px;height:34px;border-bottom:1px solid var(--line);display:flex;align-items:center;justify-content:space-between;color:#aaa;font-size:10px}
.search b{width:30px;height:30px;border-radius:50%;background:var(--orange);display:flex;align-items:center;justify-content:center}
.hweather{display:flex;align-items:center;gap:8px;color:var(--blue)}
.hweather strong{font-family:"Montserrat";font-size:22px;font-weight:600}
.hweather small{display:block;color:var(--muted);font-size:9px}

.nav{top:123px;left:0;width:1200px;height:33px;background:var(--blue)}
.nav ul{position:absolute;left:227px;width:740px;height:33px;display:flex;align-items:center;list-style:none}
.nav li{color:#fff;font-family:"Montserrat";font-size:9px;font-weight:600;text-transform:uppercase;padding:0 15px;height:33px;line-height:33px}
.nav li.on{background:var(--blue-dark)}

.breaking{top:156px;left:227px;width:740px;height:39px;display:flex;align-items:center;gap:12px;font-size:10px}
.breaking .lab{background:var(--dark);color:#fff;font-family:"Montserrat";font-weight:700;font-size:9px;padding:6px 12px}
.breaking .time{color:var(--red);font-weight:600}
.breaking .arr{margin-left:auto;display:flex;gap:3px}
.breaking .arr b,.sec-h .arr b{width:16px;height:16px;border:1px solid var(--line);display:flex;align-items:center;justify-content:center;font-size:9px;color:#999;font-weight:400}

.hero{top:195px;left:0;width:1200px;height:405px;background:linear-gradient(120deg,#c9b28a 0%,#8f7a5e 35%,#3f4a5c 65%,#b7a58a 100%)}
.hero-card{top:302px;left:227px;width:253px;height:224px;background:#fff;padding:22px 24px}
.hero-card h1{font-size:22px;line-height:1.2;font-weight:700;margin:10px 0}
.hero-card p{color:var(--muted);font-size:10px}
.hero-card .btn{display:inline-block;margin-top:18px;background:var(--red);color:#fff;font-family:"Montserrat";font-size:9px;font-weight:700;padding:8px 18px}
.hero-mini{top:490px;width:200px;height:80px;display:flex;gap:10px;color:#fff}
.hero-mini .ph{width:75px;height:62px;flex:none}
.hero-mini .t{font-family:"Montserrat";font-size:10px;font-weight:600}
.hero-mini .tag{background:#4caf50}

.sec-h{display:flex;align-items:center;gap:12px;height:20px;border-bottom:1px solid var(--line);padding-bottom:6px;margin-bottom:14px}
.sec-h h2{font-size:10px;font-weight:700;color:var(--blue);text-transform:uppercase;white-space:nowrap}
.sec-h .tabs{display:flex;gap:10px;color:#999;font-size:9px}
.sec-h .tabs .on{background:var(--blue);color:#fff;padding:0 5px}
.sec-h .arr{margin-left:auto;display:flex;gap:3px}
.sidebar-h{display:flex;height:20px;border-bottom:1px solid var(--line);margin-bottom:14px}
.sidebar-h h2{font-size:10px;font-weight:700;color:var(--ink);text-transform:uppercase}
.dark .sec-h{border-color:#333}
.dark .sec-h h2{color:#fff}
.dark .sec-h .arr b{border-color:#444}

.small{display:flex;gap:10px;margin-bottom:14px}
.small .ph{width:80px;height:56px;flex:none}
.small .title{font-size:10px;font-weight:600}
.small .title.blue{color:var(--blue)}

.grid4{display:grid;grid-template-columns:repeat(4,1fr);gap:10px}
.grid4 .ph{height:82px;margin-bottom:8px}
.grid2{display:grid;grid-template-columns:1fr 1fr;gap:17px}

.weather .now{display:flex;align-items:center;gap:14px;margin-bottom:10px}
.weather .deg{font-family:"Montserrat";font-size:30px;color:var(--blue);font-weight:600}
.weather .city{text-align:center;background:var(--soft);font-size:9px;padding:4px;margin-bottom:8px;color:#666}
.weather .days{display:grid;grid-template-columns:repeat(5,1fr);text-align:center;font-size:8px;color:#777;gap:2px}
.tabs4{display:grid;grid-template-columns:repeat(4,1fr);margin-bottom:14px}
.tabs4 span{text-align:center;font-family:"Montserrat";font-size:8px;font-weight:700;padding:6px 0;background:var(--soft);color:#777}
.tabs4 .on{background:var(--blue);color:#fff}

.video{top:2221px;left:0;width:1200px;height:276px;background:var(--dark)}
.video .strip{position:absolute;top:95px;left:-40px;display:flex;gap:6px}
.vcard{position:relative;width:236px;height:128px}
.vcard .cap{position:absolute;left:10px;bottom:10px;right:10px;color:#fff;font-family:"Montserrat";font-size:9px;font-weight:600}
.vcard .play{position:absolute;left:12px;top:12px}
.vcard.dim{opacity:.45}

.feed .it{position:relative;padding-left:18px;padding-bottom:18px;border-left:1px solid var(--line);margin-left:4px}
.feed .it::before{content:"";position:absolute;left:-4px;top:3px;width:7px;height:7px;border-radius:50%;background:var(--red)}
.feed .it .title{font-size:12px;margin-top:4px}

.social{display:grid;grid-template-columns:repeat(3,1fr);gap:4px}
.social div{height:70px;color:#fff;text-align:center;font-family:"Montserrat";font-size:9px;font-weight:600;padding-top:14px}
.social i{display:block;width:16px;height:16px;margin:0 auto 6px;background:rgba(255,255,255,.85);border-radius:50%}

.life{display:flex;gap:16px;height:129px}
.life .ph{width:170px;height:112px;flex:none}

.review{display:flex;gap:12px;margin-bottom:16px}
.review .ph{width:72px;height:90px;flex:none}
.stars{color:var(--orange);font-size:10px;letter-spacing:1px}

.pager{display:flex;gap:5px}
.pager span{width:22px;height:22px;border:1px solid var(--line);display:flex;align-items:center;justify-content:center;font-size:9px;color:#666}
.pager .on{background:var(--blue);color:#fff;border-color:var(--blue)}

.footer{top:4492px;left:0;width:1200px;height:373px;background:var(--dark);color:#aaa}
.footer h3{color:#fff;font-size:10px;font-weight:700;text-transform:uppercase;margin-bottom:16px}
.footer .small .title{color:#ddd}
.footer-bottom{position:absolute;left:0;bottom:0;width:1200px;height:58px;background:var(--darker)}
.footer-bottom .inner{position:absolute;left:227px;width:740px;top:0;height:58px;display:flex;align-items:center;gap:22px;font-size:9px;color:#888}
.follow{display:flex;gap:4px}
.follow span{width:24px;height:24px;border:1px solid #444;display:block}
.fnav{width:16px;height:16px;border:1px solid #444;display:flex;align-items:center;justify-content:center;font-size:9px}
</style>
</head>
<body>

<div class="abs topbar"><div class="inner"><div class="links"><span>Pages</span><span>Contact us</span></div><div>Register</div></div></div>

<header class="abs header">
  <div class="logo"><i></i>Vantora</div>
  <div class="search"><span>Search</span><b><svg width="12" height="12" viewBox="0 0 12 12"><circle cx="5" cy="5" r="3.6" fill="none" stroke="#fff" stroke-width="1.5"/><path d="M7.6 7.6L11 11" stroke="#fff" stroke-width="1.5"/></svg></b></div>
  <div class="hweather">
    <svg width="26" height="20" viewBox="0 0 26 20"><path d="M7 17h14a4 4 0 0 0 0-8 6 6 0 0 0-11.5 1.5A3.5 3.5 0 0 0 7 17z" fill="#9ecbf2"/></svg>
    <div><strong>+26°</strong><small>Sunny, Portland</small></div>
  </div>
</header>

<nav class="abs nav"><ul>
  <li class="on">Home</li><li>News</li><li>Sports</li><li>Art</li><li>Money</li><li>Tech</li><li>Travel</li><li>Health</li><li>Lifestyle</li><li>Movies</li><li>Media</li>
</ul></nav>

<div class="abs breaking">
  <span class="lab">BREAKING NEWS</span>
  <span class="time">● 10:45 PM</span>
  <span>Sed ut facilis consequat and cumsan justo tortor lobortis at a fresh morning brief</span>
  <span class="arr"><b>‹</b><b>›</b></span>
</div>

<div class="abs hero" role="img" aria-label="Crowd of protesters holding signs at a street rally"></div>
<article class="abs hero-card">
  <span class="tag">Politics</span>
  <h1>Republicans and Democrats judge.</h1>
  <p>Maecenas ac lacinia felis, id vulputate est. Nulla lorem magna, volutpat nec.</p>
  <span class="btn">READ MORE</span>
</article>
<article class="abs hero-mini" style="left:560px">
  <div class="ph" role="img" aria-label="Crowd gathered at an outdoor event" style="background:linear-gradient(135deg,#6f7e8c,#c3b08f)"></div>
  <div><span class="tag">World</span><div class="t">War Explains in Depth</div><div style="font-size:9px;opacity:.8">Nunc sit a tincidunt and amet vitae</div></div>
</article>
<article class="abs hero-mini" style="left:765px">
  <div class="ph" role="img" aria-label="Speaker at a podium" style="background:linear-gradient(135deg,#2e3440,#7b6c5a)"></div>
  <div><span class="tag">News</span><div class="t">Recruits Sail Ferris Streets</div><div style="font-size:9px;opacity:.8">Nunc sit a tincidunt and amet vitae</div></div>
</article>

<section class="abs" style="top:632px;left:227px;width:493px">
  <div class="sec-h"><h2>Latest News</h2><div class="tabs"><span class="on">All</span><span>World</span><span>Business</span><span>Technology</span><span>Traveling</span><span>More</span></div></div>
  <div style="display:flex;gap:10px">
    <div style="width:243px">
      <span class="tag" style="position:absolute;margin:8px">Fashion</span>
      <div class="ph" role="img" aria-label="Shopper carrying colourful bags on a yellow backdrop" style="height:178px;background:linear-gradient(135deg,#f5d400,#f0b400 60%,#e3439b)"></div>
      <div class="meta" style="margin:8px 0 4px">◷ Feb 19, 2018 <span class="count">26</span></div>
      <div class="title">Pellentesque facilisis consequat and cumsan justo tortor lobortis</div>
      <p class="excerpt" style="margin-top:6px">Curabitur commodo ante sed arcu eleifend, a tempor odio pellentesque. Nunc lacus turpis, tempor ut justo id, finibus ipsum lacinia.</p>
    </div>
    <div style="width:240px">
      <div class="small"><div class="ph" role="img" aria-label="Portrait on a city street" style="background:linear-gradient(135deg,#b89078,#5a4a44)"></div><div><div class="title blue">Curabitur commodo ante sed arcu eleifend a tempor odio pellentesque</div><div class="meta">◷ Feb 19, 2018</div></div></div>
      <div class="small"><div class="ph" role="img" aria-label="Orange car on a road" style="background:linear-gradient(135deg,#e07a3a,#7a4a36)"></div><div><div class="title">Nulla efficitur justo in sed bibendum pulvinar.</div><div class="meta">◷ Feb 19, 2018</div></div></div>
      <div class="small"><div class="ph" role="img" aria-label="Person in a bright outfit" style="background:linear-gradient(135deg,#d8587b,#f1b9a0)"></div><div><div class="title">Etiam dignissim aliquet velit sed pretium</div><div class="meta">◷ Feb 19, 2018</div></div></div>
      <div class="small"><div class="ph" role="img" aria-label="Teal workspace with a laptop" style="background:linear-gradient(135deg,#17a2a7,#0c6a72)"></div><div><div class="title">Suscipit commodo enim arcu and also eleifend tempor odio</div><div class="meta">◷ Feb 19, 2018</div></div></div>
    </div>
  </div>
</section>

<aside class="abs weather" style="top:632px;left:740px;width:227px">
  <div class="sidebar-h"><h2>Weather</h2></div>
  <div class="now">
    <svg width="70" height="50" viewBox="0 0 70 50"><circle cx="26" cy="20" r="11" fill="#ffb300"/><path d="M20 44h36a9 9 0 0 0 0-18 13 13 0 0 0-24 4 7 7 0 0 0-12 14z" fill="#bcd9f3"/></svg>
    <div><div class="deg">26°</div><div class="meta">Partly<br>sunny, 13°<br>wind 6 m/s</div></div>
  </div>
  <div class="city">PORTLAND, MAIN, AUSTRALIA</div>
  <div class="days">
    <span>MON</span><span>TUE</span><span>WED</span><span>THU</span><span>FRI</span>
    <span style="color:#9ecbf2">☁</span><span style="color:#ffb300">☀</span><span style="color:#9ecbf2">☁</span><span style="color:#9ecbf2">☂</span><span style="color:#ffb300">☀</span>
    <span>24 · 15</span><span>26 · 17</span><span>22 · 14</span><span>20 · 13</span><span>25 · 16</span>
  </div>
</aside>

<aside class="abs" style="top:900px;left:740px;width:227px">
  <div class="sidebar-h"><h2>Advertisement</h2></div>
  <div style="height:205px;margin:0 18px;background:linear-gradient(180deg,#1d4e9e,#0b2a63);color:#fff;padding:16px;font-family:Montserrat">
    <div style="font-weight:700;font-size:16px">Vantora</div>
    <div style="font-size:9px;margin-top:6px">A World Class News &amp; Magazine Template</div>
    <div class="ph" role="img" aria-label="Presenter in a news studio" style="height:80px;margin:12px 0;background:linear-gradient(135deg,#4a7ec8,#16346b)"></div>
    <span style="display:inline-block;background:var(--red);font-size:8px;font-weight:700;padding:6px 10px">BUY NOW JUST $19</span>
  </div>
</aside>

<section class="abs" style="top:1005px;left:227px;width:493px">
  <div class="sec-h"><h2>Money and Banking</h2><div class="arr"><b>‹</b><b>›</b></div></div>
  <div class="grid4">
    <div><div class="ph" role="img" aria-label="Stack of banknotes" style="background:linear-gradient(135deg,#8a9a72,#3f4b36)"></div><div class="title" style="font-size:9px;color:var(--blue)">Curabitur commodo ante sed arcu eleifend tempor</div><div class="meta">◷ Feb 19, 2018</div></div>
    <div><div class="ph" role="img" aria-label="Calculator and coins on a desk" style="background:linear-gradient(135deg,#9a8f86,#3b3633)"></div><div class="title" style="font-size:9px">Curabitur commodo ante sed arcu eleifend tempor</div><div class="meta">◷ Feb 19, 2018</div></div>
    <div><div class="ph" role="img" aria-label="Businessman in a dark suit" style="background:linear-gradient(135deg,#3b4350,#121820)"></div><div class="title" style="font-size:9px">Curabitur commodo ante sed arcu eleifend tempor</div><div class="meta">◷ Feb 19, 2018</div></div>
    <div><div class="ph" role="img" aria-label="Blue stock market chart on a screen" style="background:linear-gradient(135deg,#2f6fb2,#0d2547)"></div><div class="title" style="font-size:9px">Suscipit commodo ante sed arcu eleifend tempor</div><div class="meta">◷ Feb 19, 2018</div></div>
  </div>
</section>

<aside class="abs" style="top:1180px;left:740px;width:227px">
  <div class="tabs4"><span class="on">POPULAR</span><span>RECENT</span><span>COMMENTS</span><span>TAGS</span></div>
  <div class="small"><div class="ph" role="img" aria-label="Crowd at a stadium" style="width:70px;height:50px;background:linear-gradient(135deg,#6c7a89,#2e3742)"></div><div><div class="title blue">Curabitur commodo ante sed arcu eleifend tempor</div><div class="meta">◷ Feb 19, 2018</div></div></div>
  <div class="small"><div class="ph" role="img" aria-label="Hands typing on a laptop" style="width:70px;height:50px;background:linear-gradient(135deg,#a88f7a,#4b3e34)"></div><div><div class="title">Nulla efficitur justo in sed bibendum pulvinar.</div><div class="meta">◷ Feb 19, 2018</div></div></div>
  <div class="small"><div class="ph" role="img" aria-label="City skyline at dusk" style="width:70px;height:50px;background:linear-gradient(135deg,#d59e6b,#3c4e6e)"></div><div><div class="title">Etiam dignissim aliquet velit sed pretium</div><div class="meta">◷ Feb 19, 2018</div></div></div>
  <div class="small"><div class="ph" role="img" aria-label="Green park landscape" style="width:70px;height:50px;background:linear-gradient(135deg,#7fa862,#3b5a2d)"></div><div><div class="title">Suscipit commodo enim arcu eleifend odio</div><div class="meta">◷ Feb 19, 2018</div></div></div>
</aside>

<section class="abs" style="top:1248px;left:227px;width:493px">
  <div class="sec-h"><h2>Sports</h2><div class="arr"><b>‹</b><b>›</b></div></div>
  <div class="grid2">
    <div><div class="ph" role="img" aria-label="Football fans cheering in blue shirts" style="height:135px;background:linear-gradient(135deg,#3f73c4,#c9a27a)"></div>
      <div class="meta" style="margin:8px 0 4px">◷ Feb 19, 2018 · Admin <span class="count">14</span></div>
      <div class="title">Pellentesque facilisis consequat and cumsan justo tortor lobortis</div>
      <p class="excerpt" style="margin-top:6px">Curabitur commodo ante sed arcu eleifend, a tempor odio pellentesque. Nunc lacus turpis, tempor ut justo.</p></div>
    <div><div class="ph" role="img" aria-label="American football players in red jerseys" style="height:135px;background:linear-gradient(135deg,#b3262d,#3d6b3a)"></div>
      <div class="meta" style="margin:8px 0 4px">◷ Feb 19, 2018 · Admin <span class="count">09</span></div>
      <div class="title">Pellentesque facilisis consequat and cumsan justo tortor lobortis</div>
      <p class="excerpt" style="margin-top:6px">Curabitur commodo ante sed arcu eleifend, a tempor odio pellentesque. Nunc lacus turpis, tempor ut justo.</p></div>
  </div>
  <div class="grid2" style="margin-top:18px">
    <div>
      <div class="small"><div class="ph" role="img" aria-label="Tennis player on court" style="background:linear-gradient(135deg,#4e8a4a,#c7b27a)"></div><div><div class="title blue">Curabitur commodo ante sed arcu eleifend tempor odio</div><div class="meta">◷ Feb 19, 2018</div></div></div>
      <div class="small"><div class="ph" role="img" aria-label="Runners on a track" style="background:linear-gradient(135deg,#b4543b,#3b2a28)"></div><div><div class="title">Nulla efficitur justo in sed bibendum pulvinar.</div><div class="meta">◷ Feb 19, 2018</div></div></div>
    </div>
    <div>
      <div class="small"><div class="ph" role="img" aria-label="Red race car" style="background:linear-gradient(135deg,#c8302c,#5a5a5a)"></div><div><div class="title">Etiam dignissim aliquet velit sed pretium</div><div class="meta">◷ Feb 19, 2018</div></div></div>
      <div class="small"><div class="ph" role="img" aria-label="Basketball game in an arena" style="background:linear-gradient(135deg,#d08a3c,#2a2f3c)"></div><div><div class="title">Suscipit commodo enim arcu eleifend tempor odio</div><div class="meta">◷ Feb 19, 2018</div></div></div>
    </div>
  </div>
</section>

<aside class="abs" style="top:1590px;left:740px;width:227px">
  <div class="sidebar-h"><h2>Find us on Social</h2></div>
  <div style="border:1px solid var(--line);padding:10px">
    <div class="ph" role="img" aria-label="Page cover photo with a green landscape" style="height:70px;background:linear-gradient(135deg,#7ca95a,#cfdcb6)"></div>
    <div class="meta" style="margin:8px 0">Vantora Magazine · 12,480 likes</div>
    <div style="display:flex;gap:4px">
      <span style="width:24px;height:24px;background:#c7c7c7"></span><span style="width:24px;height:24px;background:#b5b5b5"></span><span style="width:24px;height:24px;background:#d3d3d3"></span><span style="width:24px;height:24px;background:#bdbdbd"></span><span style="width:24px;height:24px;background:#cfcfcf"></span><span style="width:24px;height:24px;background:#b0b0b0"></span>
    </div>
  </div>
</aside>

<section class="abs" style="top:1750px;left:227px;width:493px">
  <div class="sec-h"><h2>Gadgets and Technology</h2><div class="arr"><b>‹</b><b>›</b></div></div>
  <div class="grid2">
    <div>
      <div class="small"><div class="ph" role="img" aria-label="Phone on a desk" style="background:linear-gradient(135deg,#8a8f99,#2f3440)"></div><div><div class="title blue">Curabitur commodo ante sed arcu eleifend tempor odio</div><div class="meta">◷ Feb 19, 2018</div></div></div>
      <div class="small"><div class="ph" role="img" aria-label="Laptop keyboard close-up" style="background:linear-gradient(135deg,#b8b8b8,#545454)"></div><div><div class="title">Nulla efficitur justo in sed bibendum pulvinar.</div><div class="meta">◷ Feb 19, 2018</div></div></div>
      <div class="small"><div class="ph" role="img" aria-label="Person holding a tablet" style="background:linear-gradient(135deg,#c99d86,#4a3a33)"></div><div><div class="title">Etiam dignissim aliquet velit sed pretium</div><div class="meta">◷ Feb 19, 2018</div></div></div>
      <div class="small"><div class="ph" role="img" aria-label="Blue glowing circuit board" style="background:linear-gradient(135deg,#2b7fd4,#0b2142)"></div><div><div class="title">Suscipit commodo enim arcu eleifend tempor odio</div><div class="meta">◷ Feb 19, 2018</div></div></div>
    </div>
    <div>
      <div class="ph" role="img" aria-label="Smartphone with a colourful screen on a wooden table" style="height:150px;background:linear-gradient(135deg,#d8c6a9,#8c7357 60%,#6fa0d8)"></div>
      <div class="meta" style="margin:8px 0 4px">◷ Feb 19, 2018 · Admin</div>
      <div class="title" style="color:var(--blue);font-size:13px">Liberty 99 World's Bringing Some Boom Bells</div>
      <p class="excerpt" style="margin-top:6px">Curabitur commodo ante sed arcu eleifend, a tempor odio pellentesque. Nunc lacus turpis.</p>
      <span style="display:inline-block;margin-top:8px;background:var(--blue);color:#fff;font-family:Montserrat;font-size:8px;font-weight:700;padding:5px 10px">READ MORE</span>
    </div>
  </div>
</section>

<div class="abs" style="top:2124px;left:247px;width:465px;height:56px;background:linear-gradient(90deg,#1d4e9e,#0b2a63);display:flex;align-items:center;gap:18px;padding:0 16px;color:#fff">
  <span style="font-family:Montserrat;font-weight:700;font-size:16px">Vantora</span>
  <span style="font-size:9px;line-height:1.3">A World Class News &amp;<br>Magazine Template</span>
  <span style="background:var(--red);font-family:Montserrat;font-size:8px;font-weight:700;padding:6px 12px">BUY NOW JUST $19</span>
  <span class="ph" role="img" aria-label="News presenter" style="margin-left:auto;width:60px;height:44px;background:linear-gradient(135deg,#4a7ec8,#16346b)"></span>
</div>

<section class="abs video dark">
  <div class="abs" style="top:40px;left:227px;width:740px"><div class="sec-h"><h2>Video Gallery</h2><div class="arr"><b>‹</b><b>›</b></div></div></div>
  <div class="strip">
    <div class="vcard dim" role="img" aria-label="Video still of a busy street" style="background:linear-gradient(135deg,#5b6470,#23272d)"><div class="cap">Curabitur commodo ante sed arcu eleifend</div></div>
    <div class="vcard" role="img" aria-label="Video still of a concert stage" style="background:linear-gradient(135deg,#7a5e4b,#1f1a18)"><svg class="play" width="18" height="18" viewBox="0 0 18 18"><circle cx="9" cy="9" r="8.5" fill="rgba(0,0,0,.5)" stroke="#fff"/><path d="M7 5l6 4-6 4z" fill="#fff"/></svg><div class="cap">Curabitur commodo ante sed arcu eleifend</div></div>
    <div class="vcard" role="img" aria-label="Video still of a mountain road" style="background:linear-gradient(135deg,#6d8597,#2b3844)"><svg class="play" width="18" height="18" viewBox="0 0 18 18"><circle cx="9" cy="9" r="8.5" fill="rgba(0,0,0,.5)" stroke="#fff"/><path d="M7 5l6 4-6 4z" fill="#fff"/></svg><div class="cap">Curabitur commodo ante sed arcu eleifend</div></div>
    <div class="vcard" role="img" aria-label="Video still of a press conference" style="background:linear-gradient(135deg,#b39a7e,#3b3029)"><svg class="play" width="18" height="18" viewBox="0 0 18 18"><circle cx="9" cy="9" r="8.5" fill="rgba(0,0,0,.5)" stroke="#fff"/><path d="M7 5l6 4-6 4z" fill="#fff"/></svg><div class="cap">Curabitur commodo ante sed arcu eleifend</div></div>
    <div class="vcard dim" role="img" aria-label="Video still of a harbour" style="background:linear-gradient(135deg,#4f6b80,#1c2630)"><div class="cap">Curabitur commodo ante sed arcu eleifend</div></div>
  </div>
</section>

<section class="abs" style="top:2546px;left:227px;width:493px">
  <div class="sec-h"><h2>Transportation and Vehicles</h2><div class="arr"><b>‹</b><b>›</b></div></div>
  <div class="grid2" style="row-gap:14px">
    <div><div class="ph" role="img" aria-label="White truck on a highway" style="height:125px;background:linear-gradient(135deg,#a9b8c8,#5a6777)"></div><div class="title" style="margin-top:8px;color:var(--blue)">Pellentesque facilisis consequat and cumsan justo tortor lobortis</div><div class="meta" style="margin-top:4px">◷ Feb 19, 2018 · Admin <span class="count">12</span></div></div>
    <div><div class="ph" role="img" aria-label="Truck driving on a desert road" style="height:125px;background:linear-gradient(135deg,#9a8c80,#3e3a37)"></div><div class="title" style="margin-top:8px">Pellentesque facilisis consequat and cumsan justo tortor lobortis</div><div class="meta" style="margin-top:4px">◷ Feb 19, 2018 · Admin <span class="count">08</span></div></div>
    <div><div class="ph" role="img" aria-label="Silver sports car" style="height:125px;background:linear-gradient(135deg,#cfcfcf,#6a6a6a)"></div><div class="title" style="margin-top:8px">Pellentesque facilisis consequat and cumsan justo tortor lobortis</div><div class="meta" style="margin-top:4px">◷ Feb 19, 2018 · Admin <span class="count">05</span></div></div>
    <div><div class="ph" role="img" aria-label="Red classic car parked outdoors" style="height:125px;background:linear-gradient(135deg,#c2473a,#5f3a30)"></div><div class="title" style="margin-top:8px">Pellentesque facilisis consequat and cumsan justo tortor lobortis</div><div class="meta" style="margin-top:4px">◷ Feb 19, 2018 · Admin <span class="count">11</span></div></div>
    <div><div class="ph" role="img" aria-label="White coach bus on a road" style="height:125px;background:linear-gradient(135deg,#dfe4e8,#7f8a93)"></div><div class="title" style="margin-top:8px">Pellentesque facilisis consequat and cumsan justo tortor lobortis</div><div class="meta" style="margin-top:4px">◷ Feb 19, 2018 · Admin <span class="count">07</span></div></div>
    <div><div class="ph" role="img" aria-label="Busy city traffic with buses" style="height:125px;background:linear-gradient(135deg,#b9463f,#38424d)"></div><div class="title" style="margin-top:8px">Pellentesque facilisis consequat and cumsan justo tortor lobortis</div><div class="meta" style="margin-top:4px">◷ Feb 19, 2018 · Admin <span class="count">03</span></div></div>
  </div>
</section>

<aside class="abs feed" style="top:2546px;left:740px;width:227px">
  <div class="sidebar-h"><h2>News Feed</h2><span class="meta" style="margin-left:auto">Feb 19, 2018</span></div>
  <div class="it"><div class="meta">08:10</div><div class="title">Pellentesque facilisis consequat and cumsan</div><p class="excerpt">Nam sed lacus ut justo tempus.</p></div>
  <div class="it"><div class="meta">09:25</div><div class="title">Pellentesque facilisis consequat and cumsan</div><p class="excerpt">Nam sed lacus ut justo tempus.</p></div>
  <div class="it"><div class="meta">11:40</div><div class="title">Pellentesque facilisis consequat and cumsan</div><p class="excerpt">Nam sed lacus ut justo tempus.</p></div>
  <div class="it"><div class="meta">13:05</div><div class="title">Pellentesque facilisis consequat and cumsan</div><p class="excerpt">Nam sed lacus ut justo tempus.</p></div>
</aside>

<aside class="abs" style="top:3160px;left:740px;width:227px">
  <div class="sidebar-h"><h2>Stay Connected</h2></div>
  <div class="social" style="margin:0 18px">
    <div style="background:#3b5b98"><i></i>12.5K Fans</div>
    <div style="background:#1da1f2"><i></i>8.2K Followers</div>
    <div style="background:#dc4a38"><i></i>3.1K Followers</div>
    <div style="background:#0e76a8"><i></i>2.4K Members</div>
    <div style="background:#e53935"><i></i>6.7K Subscribers</div>
    <div style="background:#8bc34a"><i></i>1.9K Readers</div>
  </div>
</aside>

<section class="abs" style="top:3275px;left:227px;width:493px">
  <div class="sec-h"><h2>Home</h2><div class="arr"><b>‹</b><b>›</b></div></div>
  <div class="grid2">
    <div>
      <div class="small"><div class="ph" role="img" aria-label="Bright living room" style="background:linear-gradient(135deg,#d8c9b4,#8a7560)"></div><div><div class="title blue">Nulla efficitur justo in sed bibendum pulvinar.</div><div class="meta">◷ Feb 19, 2018</div></div></div>
      <div class="small"><div class="ph" role="img" aria-label="Kitchen interior" style="background:linear-gradient(135deg,#b48d6d,#4a3a2e)"></div><div><div class="title">Nulla efficitur justo in sed bibendum pulvinar.</div><div class="meta">◷ Feb 19, 2018</div></div></div>
    </div>
    <div>
      <div class="small"><div class="ph" role="img" aria-label="Modern house exterior" style="background:linear-gradient(135deg,#9fb0bf,#4d5a66)"></div><div><div class="title">Suscipit commodo enim arcu and eleifend tempor odio</div><div class="meta">◷ Feb 19, 2018</div></div></div>
      <div class="small"><div class="ph" role="img" aria-label="Garden with flowers" style="background:linear-gradient(135deg,#c96b5a,#4f6e3c)"></div><div><div class="title">Suscipit commodo enim arcu and eleifend tempor odio</div><div class="meta">◷ Feb 19, 2018</div></div></div>
    </div>
  </div>
</section>

<aside class="abs" style="top:3420px;left:740px;width:227px">
  <div class="sidebar-h"><h2>Latest Articles</h2></div>
  <div style="position:relative;height:140px;margin-bottom:14px">
    <div class="ph" role="img" aria-label="Woman working at a desk" style="position:absolute;inset:0;background:linear-gradient(135deg,#6b6e78,#1e2026)"></div>
    <div class="title" style="position:absolute;left:10px;right:10px;bottom:10px;color:#fff;font-size:11px">Pellentesque facilisis consequat and cumsan justo tortor.</div>
  </div>
  <div class="small"><div class="ph" role="img" aria-label="Mountain view" style="width:60px;height:44px;background:linear-gradient(135deg,#8aa4c0,#3b4a5a)"></div><div><div class="title">Etiam dignissim aliquet velit sed</div><div class="meta">◷ Feb 19, 2018</div></div></div>
  <div class="small"><div class="ph" role="img" aria-label="Coffee cup on a table" style="width:60px;height:44px;background:linear-gradient(135deg,#a57b5a,#3e2a1e)"></div><div><div class="title">Suscipit commodo enim arcu tempor</div><div class="meta">◷ Feb 19, 2018</div></div></div>
  <div class="small"><div class="ph" role="img" aria-label="Beach at sunset" style="width:60px;height:44px;background:linear-gradient(135deg,#e3a15a,#4a6a8c)"></div><div><div class="title">Nulla efficitur justo in bibendum</div><div class="meta">◷ Feb 19, 2018</div></div></div>
  <div class="small"><div class="ph" role="img" aria-label="City at night" style="width:60px;height:44px;background:linear-gradient(135deg,#3c4b6e,#0f1424)"></div><div><div class="title">Curabitur commodo ante sed arcu</div><div class="meta">◷ Feb 19, 2018</div></div></div>
</aside>

<section class="abs" style="top:3486px;left:227px;width:493px">
  <div class="sec-h"><h2>Life Style</h2><div class="arr"><b>‹</b><b>›</b></div></div>
  <div class="life"><div class="ph" role="img" aria-label="Friends laughing outdoors" style="background:linear-gradient(135deg,#c5a17f,#5d6b4a)"></div><div><div class="title">Pellentesque facilisis consequat and cumsan justo tortor lobortis</div><div class="meta" style="margin:5px 0">◷ Feb 19, 2018 · Admin</div><p class="excerpt">Aliquam et velit sollicitudin, efficitur tortor, porta ipsum. Integer tristique felis quis risus interdum tempus.</p><span class="count">18</span></div></div>
  <div class="life"><div class="ph" role="img" aria-label="Woman using a laptop on a sofa" style="background:linear-gradient(135deg,#9c9a98,#3f3a36)"></div><div><div class="title">Pellentesque facilisis consequat and cumsan justo tortor lobortis</div><div class="meta" style="margin:5px 0">◷ Feb 19, 2018 · Admin</div><p class="excerpt">Aliquam et velit sollicitudin, efficitur tortor, porta ipsum. Integer tristique felis quis risus interdum tempus.</p><span class="count">06</span></div></div>
  <div class="life"><div class="ph" role="img" aria-label="Family sharing a meal" style="background:linear-gradient(135deg,#d3a37a,#6a4a34)"></div><div><div class="title">Pellentesque facilisis consequat and cumsan justo tortor lobortis</div><div class="meta" style="margin:5px 0">◷ Feb 19, 2018 · Admin</div><p class="excerpt">Aliquam et velit sollicitudin, efficitur tortor, porta ipsum. Integer tristique felis quis risus interdum tempus.</p><span class="count">11</span></div></div>
  <div class="life"><div class="ph" role="img" aria-label="Couple jumping on a beach under blue sky" style="background:linear-gradient(135deg,#5aa6e0,#e2a35c)"></div><div><div class="title">Pellentesque facilisis consequat and cumsan justo tortor lobortis</div><div class="meta" style="margin:5px 0">◷ Feb 19, 2018 · Admin</div><p class="excerpt">Aliquam et velit sollicitudin, efficitur tortor, porta ipsum. Integer tristique felis quis risus interdum tempus.</p><span class="count">09</span></div></div>
  <div class="life"><div class="ph" role="img" aria-label="Man in a suit in an office" style="background:linear-gradient(135deg,#8c8f95,#2e3036)"></div><div><div class="title">Pellentesque facilisis consequat and cumsan justo tortor lobortis</div><div class="meta" style="margin:5px 0">◷ Feb 19, 2018 · Admin</div><p class="excerpt">Aliquam et velit sollicitudin, efficitur tortor, porta ipsum. Integer tristique felis quis risus interdum tempus.</p><span class="count">04</span></div></div>
  <div class="life"><div class="ph" role="img" aria-label="Shopping in a red boutique" style="background:linear-gradient(135deg,#c23a3a,#4a2a2a)"></div><div><div class="title">Pellentesque facilisis consequat and cumsan justo tortor lobortis</div><div class="meta" style="margin:5px 0">◷ Feb 19, 2018 · Admin</div><p class="excerpt">Aliquam et velit sollicitudin, efficitur tortor, porta ipsum. Integer tristique felis quis risus interdum tempus.</p><span class="count">15</span></div></div>
  <div class="life"><div class="ph" role="img" aria-label="Woman holding a camera" style="background:linear-gradient(135deg,#d9c8b6,#7a6250)"></div><div><div class="title">Pellentesque facilisis consequat and cumsan justo tortor lobortis</div><div class="meta" style="margin:5px 0">◷ Feb 19, 2018 · Admin</div><p class="excerpt">Aliquam et velit sollicitudin, efficitur tortor, porta ipsum. Integer tristique felis quis risus interdum tempus.</p><span class="count">02</span></div></div>
</section>

<aside class="abs" style="top:3995px;left:740px;width:227px">
  <div class="sidebar-h"><h2>Latest Reviews</h2></div>
  <div class="review"><div class="ph" role="img" aria-label="Model in a wedding dress" style="background:linear-gradient(135deg,#e9ddd2,#9a8676)"></div><div><div class="stars">★★★★★</div><div class="title">Wedding Fashion</div><p class="excerpt">Nunc sit a tincidunt and amet vitae</p></div></div>
  <div class="review"><div class="ph" role="img" aria-label="Guests at an evening party" style="background:linear-gradient(135deg,#c88a5a,#3a2a22)"></div><div><div class="stars">★★★★☆</div><div class="title">Party Time</div><p class="excerpt">Nunc sit a tincidunt and amet vitae</p></div></div>
  <div class="review"><div class="ph" role="img" aria-label="Fashion model in a bright dress" style="background:linear-gradient(135deg,#d95a7a,#5a2a3a)"></div><div><div class="stars">★★★★★</div><div class="title">Fashion Models</div><p class="excerpt">Nunc sit a tincidunt and amet vitae</p></div></div>
</aside>

<div class="abs pager" style="top:4440px;left:227px"><span class="on">1</span><span>2</span><span>3</span><span>…</span><span>15</span><span>›</span></div>

<footer class="abs footer">
  <div class="abs" style="top:44px;left:227px;width:210px">
    <p style="font-size:10px;line-height:1.7">Vivamus dapibus tempus magna, in tristique lacus tincidunt quis. Nullam sed dolor a nunc porta lacinia. Fusce semper, sapien in luctus gravida, lorem sem tempus velit, quis porta mauris augue ut nisi.</p>
    <h3 style="margin-top:40px">Follow Us</h3>
    <div class="follow"><span></span><span></span><span></span><span></span><span></span></div>
  </div>
  <div class="abs" style="top:44px;left:480px;width:230px">
    <h3>Random Posts</h3>
    <div class="small"><div class="ph" role="img" aria-label="Man portrait outdoors" style="width:70px;height:50px;background:linear-gradient(135deg,#6f6a66,#2b2826)"></div><div><div class="title">Nulla efficitur justo in sed bibendum pulvinar.</div><div class="meta">◷ Feb 19, 2018</div></div></div>
    <div class="small"><div class="ph" role="img" aria-label="Woman in a cafe" style="width:70px;height:50px;background:linear-gradient(135deg,#9a7b64,#3a2e26)"></div><div><div class="title">Nulla efficitur justo in sed bibendum pulvinar.</div><div class="meta">◷ Feb 19, 2018</div></div></div>
    <div class="small"><div class="ph" role="img" aria-label="Group of colleagues" style="width:70px;height:50px;background:linear-gradient(135deg,#7c8794,#2d333a)"></div><div><div class="title">Nulla efficitur justo in sed bibendum pulvinar.</div><div class="meta">◷ Feb 19, 2018</div></div></div>
  </div>
  <div class="abs" style="top:44px;left:740px;width:227px">
    <div style="display:flex"><h3>Slideshow</h3><span style="margin-left:auto;display:flex;gap:3px"><b class="fnav">‹</b><b class="fnav">›</b></span></div>
    <div style="position:relative;height:150px">
      <div class="ph" role="img" aria-label="Woman looking at a phone in the city" style="position:absolute;inset:0;background:linear-gradient(135deg,#5d6470,#17191d)"></div>
      <div class="title" style="position:absolute;left:10px;right:10px;bottom:12px;color:#fff;font-size:11px">Pellentesque facilisis consequat and cumsan justo tortor lobortis</div>
    </div>
  </div>
  <div class="footer-bottom"><div class="inner">
    <span style="color:#fff">Home</span><span>Contact</span><span>Privacy</span><span>Reviews</span><span>Services</span>
    <span style="margin-left:auto">© 2018 Vantora. All rights reserved.</span>
  </div></div>
</footer>

</body>
</html>
```